Business Cards

Need business card design that I can update for new employees and details. Needs to incorporate our logo, be bright and fun (in line with tourism and holidays)
Would like a Map of Western Australia on the front with locations all the caravan parks we own (just purchased Tom Price so please include that as well as others listed on our website).
Target Market(s)
Famillies
Contact Information for Business Card
5 Cards -
Neil Perrow (Director) e: perrow@wattlebay.com.au p: 0491 570 156
Mira Perrow (Director) e: perrow@wattlebay.com.au p: 0491 570 157
Owen Halvey (General Manager) e: halvey@wattlebay.com.au p: 0491 570 158
Helen Halvey (General Manager) e: halvey@wattlebay.com.au p: 0491 570 159
Colin Danby (Training and Operations Manager) - e: danby@wattlebay.com.au p:0491 570 110
Colors
Look and feel

```html
<!DOCTYPE html>
<html lang="en">
<head>
<meta charset="utf-8">
<title>Wattle Bay Tourist Parks – Business Cards</title>
<link rel="stylesheet" href="https://fonts.googleapis.com/css2?family=Marcellus&family=Lora:wght@400;700&display=swap">
<style>
  :root {
    --backdrop: #e9e9ea;
    --teal: #2fb3c3;
    --teal-deep: #2aa5b5;
    --sea-green: #5fb3a0;
    --card-white: #f4f4f4;
    --map-tint: #e6e8e8;
    --ink: #4a4a4a;
    --ink-soft: #6a6a6a;
    --white: #ffffff;
  }
  * { box-sizing: border-box; margin: 0; padding: 0; }
  html, body { width: 1200px; height: 726px; overflow: hidden; }
  body {
    background: var(--backdrop);
    font-family: "Lora", Georgia, serif;
    position: relative;
  }
  .card {
    position: absolute;
    top: 204px;
    width: 520px;
    height: 318px;
    overflow: hidden;
    box-shadow: 0 2px 10px rgba(0,0,0,0.12);
  }

  /* Front */
  .card-front {
    left: 50px;
    background: linear-gradient(160deg, var(--teal) 0%, #45b5bb 55%, var(--sea-green) 100%);
    color: var(--white);
    text-align: center;
  }
  .front-brand {
    position: absolute;
    top: 62px; left: 0; right: 0;
    display: flex; flex-direction: column; align-items: center;
  }
  .brand-square {
    width: 64px; height: 64px;
    border: 3px solid var(--white);
    margin-bottom: 14px;
  }
  .brand-name {
    font-family: "Marcellus", Georgia, serif;
    font-size: 40px;
    letter-spacing: 3px;
    line-height: 1;
  }
  .brand-sub {
    font-family: "Marcellus", Georgia, serif;
    font-size: 15px;
    letter-spacing: 6px;
    margin-top: 6px;
  }
  .park-list {
    position: absolute;
    top: 226px; left: 0; right: 0;
    font-size: 14px;
    line-height: 1.45;
    letter-spacing: 0.3px;
  }

  /* Back */
  .card-back {
    left: 630px;
    background: var(--card-white);
    color: var(--ink);
  }
  .map-area {
    position: absolute;
    top: 0; right: 0;
    width: 200px; height: 220px;
  }
  .back-bands { position: absolute; inset: 0; }
  .back-brand {
    position: absolute;
    top: 78px; left: 36px;
    display: flex; align-items: center; gap: 16px;
  }
  .back-brand .brand-square {
    width: 78px; height: 78px;
    border: 0;
    background: var(--teal-deep);
    margin: 0;
  }
  .back-brand .brand-name { color: var(--ink); font-size: 34px; }
  .back-brand .brand-sub { color: var(--ink); font-size: 13px; letter-spacing: 5px; }
  .contact-list {
    position: absolute;
    top: 148px; left: 318px;
    list-style: none;
    font-size: 13px;
    color: var(--ink);
  }
  .contact-list li {
    display: flex; align-items: center; gap: 10px;
    height: 19px;
  }
  .contact-list svg { width: 12px; height: 12px; flex: none; }
  .person {
    position: absolute;
    left: 56px; top: 226px;
  }
  .person-name { font-size: 25px; font-weight: 700; color: var(--ink); }
  .person-role { font-size: 11px; color: var(--ink-soft); margin-top: 2px; }
  .tagline {
    position: absolute;
    left: 330px; top: 246px;
    font-size: 13px;
    color: var(--white);
  }
</style>
</head>
<body>

<section class="card card-front" aria-label="Business card front">
  <div class="front-brand">
    <div class="brand-square"></div>
    <div class="brand-name">WATTLE BAY</div>
    <div class="brand-sub">TOURIST PARKS</div>
  </div>
  <p class="park-list">
    Geraldton | Horrocks | Esperance | Jurien | Margaret River<br>
    Walpole | Saltbush Beach House
  </p>
</section>

<section class="card card-back" aria-label="Business card back">
  <svg class="map-area" viewBox="0 0 200 220" role="img" aria-label="Faint map of the Western Australian coastline">
    <defs>
      <linearGradient id="mapFade" x1="0" y1="0" x2="1" y2="1">
        <stop offset="0" stop-color="var(--map-tint)" stop-opacity="0.2"/>
        <stop offset="1" stop-color="var(--map-tint)" stop-opacity="1"/>
      </linearGradient>
    </defs>
    <rect width="200" height="220" fill="url(#mapFade)"/>
  </svg>

  <svg class="back-bands" viewBox="0 0 520 318" preserveAspectRatio="none" aria-hidden="true">
    <polygon points="0,304 284,290 290,318 0,318" fill="var(--teal-deep)"/>
    <polygon points="298,234 520,214 520,318 294,318" fill="var(--sea-green)"/>
  </svg>

  <div class="back-brand">
    <div class="brand-square"></div>
    <div>
      <div class="brand-name">WATTLE BAY</div>
      <div class="brand-sub">TOURIST PARKS</div>
    </div>
  </div>

  <ul class="contact-list">
    <li>
      <svg viewBox="0 0 12 12" aria-hidden="true"><path d="M2 1h2.5l1 2.5-1.5 1a6 6 0 0 0 3.5 3.5l1-1.5 2.5 1V11A9 9 0 0 1 1 2z" fill="var(--teal-deep)"/></svg>
      0491 570 158
    </li>
    <li>
      <svg viewBox="0 0 12 12" aria-hidden="true"><circle cx="6" cy="6" r="5" fill="none" stroke="var(--teal-deep)" stroke-width="1.2"/><path d="M1 6h10M6 1c-2.5 3-2.5 7 0 10M6 1c2.5 3 2.5 7 0 10" fill="none" stroke="var(--teal-deep)" stroke-width="1"/></svg>
      www.wattlebay.com.au
    </li>
    <li>
      <svg viewBox="0 0 12 12" aria-hidden="true"><rect x="0.5" y="2" width="11" height="8" fill="var(--teal-deep)"/><path d="M0.5 2 6 6.5 11.5 2" fill="none" stroke="var(--card-white)" stroke-width="1"/></svg>
      halvey@wattlebay.com.au
    </li>
  </ul>

  <div class="person">
    <div class="person-name">Owen Halvey</div>
    <div class="person-role">General Manager</div>
  </div>

  <div class="tagline">Best Tourist Parks</div>
</section>

</body>
</html>
```